Flyer for an anniversary promotion

2nd year anniversary promotion flyer for Copperleaf Dental (logo attached)
Size A4
Promotion runs from Now until 31st Dec 2024
Leave room for actual promotional text which will be in multiple languages (~50 words)
Brand associations
Modern, classy, high quality service, customer care

NOTE - Company SELLS to dental clinics but Copperleaf is a dental products company, not dentists/dental clinics/etc.

Plumvistar wants this to be 300+ words

Target Market(s)

Dental clinics

Industry/Entity Type

Dental

Requirements
Should not have
• Don't use images of teeth

```html
<!DOCTYPE html>
<html lang="en">
<head>
<meta charset="utf-8">
<title>Copperleaf Dental – 2nd Anniversary Promotion Flyer</title>
<link href="https://fonts.googleapis.com/css2?family=Archivo:wght@300;400;500;600;700;800;900&display=swap" rel="stylesheet">
<style>
  :root{
    --navy:#041a2b;
    --blue:#1479be;
    --blue-text:#1b7cc1;
    --ink:#1c2a3a;
    --white:#ffffff;
    --stage:#e4e5e7;
    --gold-dark:#b9741f;
    --gold:#e7a43a;
    --gold-light:#fdf1a8;
    --rule:#b9bcc1;
  }
  *{margin:0;padding:0;box-sizing:border-box;}
  html,body{width:1200px;height:1142px;overflow:hidden;background:var(--stage);}
  body{font-family:"Archivo",Arial,sans-serif;color:var(--ink);}
  .flyer{position:absolute;left:208px;top:16px;width:784px;height:1110px;background:var(--white);overflow:hidden;box-shadow:0 4px 18px rgba(0,0,0,.18);}
  .abs{position:absolute;}

  /* header */
  .header-art{left:0;top:0;}
  .sparkle-field{left:0;top:0;width:300px;height:250px;background:radial-gradient(ellipse at 40% 40%,rgba(231,164,58,.22),rgba(4,26,43,0) 70%);}
  .celebrate{left:43px;top:34px;font-size:22px;font-weight:600;color:var(--white);}
  .big-2nd{left:38px;top:52px;font-size:128px;font-weight:800;line-height:1;letter-spacing:-7px;
    background:linear-gradient(180deg,#fff6c8 0%,#f2c23e 45%,#c98b1d 75%,#f6d36a 100%);
    -webkit-background-clip:text;background-clip:text;color:transparent;}
  .anniversary{left:43px;top:161px;font-size:35px;font-weight:700;color:var(--blue-text);}
  .with-brand{left:42px;top:201px;font-size:19px;font-weight:700;color:var(--white);}
  .header-divider{left:295px;top:41px;width:1px;height:181px;background:rgba(255,255,255,.55);}
  .intro{left:339px;top:67px;width:300px;font-size:15.3px;line-height:17.3px;color:var(--white);}

  /* categories */
  .category{top:282px;font-size:21px;font-weight:700;line-height:21px;}
  .category.blue{color:var(--blue-text);}
  .category.navy{color:var(--navy);}
  .category-rule{top:276px;width:1px;height:58px;background:var(--rule);}

  /* promotion band */
  .period-band{left:0;top:364px;width:784px;height:62px;background:var(--navy);}
  .period-pill{left:-40px;top:355px;width:458px;height:78px;border-radius:0 40px 40px 0;background:linear-gradient(90deg,var(--gold) 0%,var(--gold-light) 70%,var(--gold-dark) 100%);}
  .period-pill-inner{left:-40px;top:360px;width:448px;height:68px;border-radius:0 34px 34px 0;background:var(--blue);}
  .period-label{left:37px;top:377px;font-size:32px;font-weight:800;color:var(--white);letter-spacing:.3px;}
  .period-dates{left:467px;top:377px;font-size:21px;line-height:20px;color:var(--white);letter-spacing:-.3px;}
  .period-dates b{font-weight:700;}

  /* offers */
  .offers-title{left:37px;top:453px;font-size:42px;font-weight:300;color:var(--blue-text);letter-spacing:-.8px;}
  .offers-rule{left:37px;top:516px;width:451px;height:1px;background:var(--rule);}
  .offers-lead{left:37px;top:530px;width:400px;font-size:15.3px;line-height:19px;color:var(--ink);letter-spacing:-.2px;}

  /* why panel */
  .why{left:546px;top:479px;width:240px;height:503px;border-radius:112px 0 0 112px;background:linear-gradient(180deg,var(--gold) 0%,var(--gold-light) 25%,var(--gold-dark) 55%,var(--gold) 80%,var(--gold-light) 100%);}
  .why-inner{position:absolute;left:8px;top:7px;right:0;bottom:0;border-radius:104px 0 0 104px;overflow:hidden;background:var(--blue);}
  .why-head{height:136px;background:var(--navy);text-align:right;padding:23px 36px 0 0;font-size:25px;font-weight:800;line-height:23px;color:var(--white);}
  .why-head .accent{color:var(--blue-text);}
  .why-list{padding:22px 36px 0 20px;text-align:right;color:var(--white);font-size:12.5px;line-height:15.8px;}
  .why-item{padding-bottom:14px;margin-bottom:15px;border-bottom:1px solid rgba(255,255,255,.6);}
  .why-item:last-child{border-bottom:0;}
  .why-item b{font-weight:700;}
  .why-item span{font-weight:300;}

  /* brand + footer */
  .brand{left:48px;top:1046px;display:flex;align-items:center;gap:10px;font-size:22px;font-weight:700;color:var(--navy);letter-spacing:.5px;}
  .brand-square{width:14px;height:14px;background:var(--blue);}
  .footer-rule{left:318px;top:1030px;width:466px;height:1px;background:var(--rule);}
  .footer-col-rule{top:1039px;width:1px;height:48px;background:var(--rule);}
  .contact{font-size:10.4px;line-height:13px;color:var(--navy);display:flex;gap:6px;align-items:flex-start;}
  .contact svg{flex:none;margin-top:1px;}
</style>
</head>
<body>
<main class="flyer">
  <svg class="abs header-art" width="784" height="258" viewBox="0 0 784 258" aria-hidden="true">
    <defs>
      <linearGradient id="goldEdge" x1="0" y1="1" x2="1" y2="0">
        <stop offset="0" stop-color="#b9741f"/>
        <stop offset=".45" stop-color="#fdf1a8"/>
        <stop offset=".75" stop-color="#f2c23e"/>
        <stop offset="1" stop-color="#d98c2a"/>
      </linearGradient>
    </defs>
    <rect x="700" y="0" width="84" height="177" fill="#1479be"/>
    <path d="M0,0 H762 C742,150 640,250 500,250 H0 Z" fill="#041a2b"/>
    <path d="M762,0 C742,150 640,250 500,250 H0" fill="none" stroke="url(#goldEdge)" stroke-width="6"/>
  </svg>
  <div class="abs sparkle-field" role="img" aria-label="Scattered gold glitter sparkles decoration"></div>

  <div class="abs celebrate">Celebrate Our</div>
  <div class="abs big-2nd">2nd</div>
  <div class="abs anniversary">Anniversary</div>
  <div class="abs with-brand">with Copperleaf Dental!</div>
  <div class="abs header-divider"></div>
  <p class="abs intro">Join us in celebrating 2nd successful year of providing top-tier dental products that enhance the quality of care in clinics nationwide. Copperleaf Dental has spent the past two years dedicated to delivering high-quality, modern solutions that dental clinics can trust to support their patients' smiles.</p>

  <div class="abs category blue" style="left:37px;">FIXED<br>RESTORATIONS</div>
  <div class="abs category-rule" style="left:221px;"></div>
  <div class="abs category navy" style="left:244px;">IMPLANT<br>RESTORATIONS</div>
  <div class="abs category-rule" style="left:428px;"></div>
  <div class="abs category blue" style="left:452px;">DIGITAL<br>DENTISTRY</div>
  <div class="abs category-rule" style="left:593px;"></div>
  <div class="abs category navy" style="left:617px;">DENTURES &amp;<br>OTHERS</div>

  <div class="abs period-band"></div>
  <div class="abs period-pill"></div>
  <div class="abs period-pill-inner"></div>
  <div class="abs period-label">PROMOTION PERIOD</div>
  <div class="abs period-dates">Available from <b>now</b> until<br><b>December 31, 2024.</b></div>

  <h1 class="abs offers-title">Special Anniversary Offers</h1>
  <div class="abs offers-rule"></div>
  <p class="abs offers-lead">To show our appreciation for your support, we’re offering exclusive promotions for a limited time.</p>

  <aside class="abs why">
    <div class="why-inner">
      <h2 class="why-head">Why<br><span class="accent">Choose</span><br>Copperleaf<br>Dental?</h2>
      <div class="why-list">
        <p class="why-item"><b>Dedicated to Dental Clinics:</b><br><span>Tailored solutions that align with your clinic’s needs, ensuring your patients receive the best possible care.</span></p>
        <p class="why-item"><b>Modern &amp; Classy Products:</b><br><span>Designed to complement the standards of high-quality dental clinics.</span></p>
        <p class="why-item"><b>Exceptional<br>Customer Care:</b><br><span>We prioritize your satisfaction and success with products you can rely on.</span></p>
      </div>
    </div>
  </aside>

  <div class="abs brand"><span class="brand-square"></span>Copperleaf Dental</div>

  <div class="abs footer-rule"></div>
  <div class="abs contact" style="left:318px;top:1050px;">
    <svg width="11" height="13" viewBox="0 0 11 13" aria-hidden="true"><path d="M5.5 12 C2 8 1 6.3 1 4.6 A4.5 4.5 0 0 1 10 4.6 C10 6.3 9 8 5.5 12Z" fill="none" stroke="#1479be" stroke-width="1"/><circle cx="5.5" cy="4.6" r="1.6" fill="none" stroke="#1479be"/></svg>
    <span>Suite 804, Harbourline Tower,<br>215 Lai Chi Kok Road,<br>Sham Shui Po, Kowloon</span>
  </div>
  <div class="abs footer-col-rule" style="left:483px;"></div>
  <div class="abs contact" style="left:508px;top:1050px;">
    <svg width="12" height="10" viewBox="0 0 12 10" aria-hidden="true"><rect x=".5" y="1" width="11" height="8" fill="none" stroke="#1479be"/><path d="M.5 1 L6 5.5 L11.5 1" fill="none" stroke="#1479be"/></svg>
    <span>info@copperleaf.com.hk</span>
  </div>
  <div class="abs contact" style="left:508px;top:1074px;">
    <svg width="12" height="12" viewBox="0 0 12 12" aria-hidden="true"><circle cx="6" cy="6" r="5.2" fill="none" stroke="#1479be"/><ellipse cx="6" cy="6" rx="2.3" ry="5.2" fill="none" stroke="#1479be"/><path d="M.8 6 H11.2" stroke="#1479be"/></svg>
    <span>www.copperleaf.com.hk</span>
  </div>
  <div class="abs footer-col-rule" style="left:659px;"></div>
  <div class="abs contact" style="left:683px;top:1050px;">
    <svg width="11" height="11" viewBox="0 0 11 11" aria-hidden="true"><path d="M2.2 1 L4 3.2 L3 4.5 C3.8 6 5 7.2 6.5 8 L7.8 7 L10 8.8 L9 10 C4.5 9.8 1.2 6.5 1 2 Z" fill="none" stroke="#1479be" stroke-linejoin="round"/></svg>
    <span>3620 4718</span>
  </div>
</main>
</body>
</html>
```